Graphic design for "How It Works" for VelmoraAttire.net*

VelmoraAttire.net website is for selling custom designer outfits for women and girls in all countries, customers can choose existing designs on this website and customize to their measurements. Customers can also provide their own designs and measurements and our expert designers and tailors get the outfit stitched and delivered to the customer.

We wanted to explain how this entire process works in 4 steps in the form of graphic design with little heading and text describing each step.

Step 1: Select Dress
Its time to choose the beauty you want to adorn yourself with. We have a wide collection of premium dresses, colours and accessories. There is something for everyone! All you need to do is pick. If you can’t find what you are looking for then you can share a picture of what you want, we will get it done whatever you want.

Step 2: Customization
Everyone is different; hence we realise the need for customization of the design and size. Here you select exactly how you want your dress to be. From sleeves to cuts, everything will be done as per your wish. Enter your measurements, lo and behold! You’re done. Leave your comments for even more customization.

Step 3: Designer Consultation
We as a user-friendly brand, aspire to provide the best of services to our clients. Our expert lady designers will help you for everything right from selecting of fabric to design of dress to necessary accessories. Our designers are just a call away!

Step 4: Stitch and Deliver
After you have placed your order, we confirm and verify the details. The boutique completes your order, sends it to us and we deliver it to your doorstep. We also have a team of designers in-house to cater to your premium dressing needs.

```html
<!DOCTYPE html>
<html lang="en">
<head>
<meta charset="utf-8">
<title>How It Works – VelmoraAttire.net</title>
<link rel="stylesheet" href="https://fonts.googleapis.com/css2?family=Montserrat:wght@700;800;900&family=Poppins:wght@500;600;700&family=PT+Serif&display=swap">
<style>
  :root {
    --pink: #c9538a;
    --pink-deep: #b83f77;
    --pink-soft: #dc86ae;
    --ink: #2e3236;
    --paper: #ffffff;
    --mist: #ececec;
    --body-text: #3a3a3a;
  }
  * { box-sizing: border-box; margin: 0; padding: 0; }
  html, body { width: 1200px; height: 370px; overflow: hidden; background: var(--paper); }
  .canvas { position: relative; width: 1200px; height: 370px; overflow: hidden; background: var(--paper); }

  .decor { position: absolute; inset: 0; }

  .brand { position: absolute; left: 29px; top: 35px; display: flex; align-items: center; gap: 11px; }
  .brand-dot { width: 24px; height: 24px; border-radius: 50%; background: var(--pink); }
  .brand-name { font-family: "Poppins", sans-serif; font-weight: 600; font-size: 21px; color: var(--ink); letter-spacing: -0.2px; }

  .question { position: absolute; left: 27px; top: 160px; font-family: "Montserrat", sans-serif; font-weight: 900; font-size: 145px; line-height: 1; color: var(--paper); }
  .title { position: absolute; left: 128px; top: 184px; width: 74px; font-family: "Montserrat", sans-serif; color: var(--ink); }
  .title-how { display: block; font-weight: 800; font-size: 24px; letter-spacing: 2px; line-height: 1; }
  .title-it { display: block; font-weight: 900; font-style: italic; font-size: 64px; line-height: 0.82; color: var(--pink); margin-top: 5px; letter-spacing: -1px; }
  .title-works { display: block; font-weight: 800; font-size: 13.5px; letter-spacing: 1.6px; line-height: 1; margin-top: 6px; }

  .step { position: absolute; top: 0; width: 190px; height: 370px; }
  .step-1 { left: 260px; } .step-2 { left: 499px; } .step-3 { left: 740px; } .step-4 { left: 981px; }

  .step-art { position: absolute; left: 0; top: 18px; width: 192px; height: 156px; border-radius: 50%;
    background: radial-gradient(ellipse at 50% 55%, #f4dbe7 0%, #e9e9e9 55%, #ececec 100%); }

  .step-card { position: absolute; left: 6px; top: 208px; width: 180px; height: 99px; background: var(--paper);
    box-shadow: 0 1px 5px rgba(0,0,0,0.22); padding: 15px 10px 0 10px; }
  .step-card p { font-family: "PT Serif", serif; font-size: 7.7px; line-height: 9.7px; color: var(--body-text); text-align: justify; }

  .step-tab { position: absolute; left: 0; top: 191px; height: 24px; width: 131px; border-radius: 0 12px 12px 0;
    font-family: "Poppins", sans-serif; font-weight: 500; font-size: 7.8px; color: var(--paper); white-space: nowrap;
    display: flex; align-items: center; padding-left: 7px; z-index: 2; }
  .step-tab::after { content: ""; position: absolute; left: 0; bottom: -7px; width: 6px; height: 7px; background: var(--ink); }
  .step-tab em { font-weight: 700; margin-right: 3px; }
  .tab-pink { background: var(--pink); }
  .tab-dark { background: var(--ink); }

  .step-number { position: absolute; left: 76px; top: 319px; width: 37px; height: 37px; border-radius: 50%;
    background: var(--pink); border: 2.5px solid var(--paper);
    box-shadow: -3px 1px 0 var(--ink), 0 0 0 0.5px #ddd;
    font-family: "Montserrat", sans-serif; font-weight: 800; font-size: 24px; color: var(--paper);
    display: flex; align-items: center; justify-content: center; }
</style>
</head>
<body>
<main class="canvas">
  <svg class="decor" width="1200" height="370" viewBox="0 0 1200 370" aria-hidden="true">
    <defs>
      <linearGradient id="blob-fill" x1="0" y1="0" x2="1" y2="1">
        <stop offset="0" stop-color="#d66fa0"/>
        <stop offset="1" stop-color="#c04a80"/>
      </linearGradient>
    </defs>
    <path d="M0 128 C55 118 118 132 138 182 C156 228 118 276 148 312 C176 344 228 330 250 370 L0 370 Z" fill="url(#blob-fill)"/>
    <path d="M0 250 C40 230 90 260 100 300 C112 345 160 350 180 370 L0 370 Z" fill="#d87aa7" opacity="0.55"/>
    <circle cx="163" cy="236" r="67" fill="var(--paper)"/>
    <circle cx="163" cy="236" r="67" fill="none" stroke="#2e3236" stroke-width="0.9" stroke-dasharray="3 3"/>
    <ellipse cx="62" cy="301" rx="34" ry="5" fill="#8e2e5c" opacity="0.6"/>
    <circle cx="0" cy="0" r="17" fill="var(--pink)"/>
    <circle cx="1200" cy="0" r="18" fill="var(--pink)"/>
    <circle cx="1200" cy="370" r="20" fill="var(--pink)"/>
  </svg>

  <header class="brand">
    <span class="brand-dot"></span>
    <span class="brand-name">velmoraattire</span>
  </header>

  <div class="question" aria-hidden="true">?</div>
  <h1 class="title">
    <span class="title-how">HOW</span>
    <span class="title-it">IT</span>
    <span class="title-works">WORKS?</span>
  </h1>

  <section class="step step-1">
    <div class="step-art" role="img" aria-label="Illustration of a woman browsing dresses on a large website screen"></div>
    <h2 class="step-tab tab-pink"><em>STEP 1:</em> Select Dress</h2>
    <div class="step-card"><p>Its time to choose the beauty you want to adorn yourself with. We have a wide collection of premium dresses, colours and accessories. There is something for everyone! All you need to do is pick. If you can’t find what you are looking for then you can share a picture of what you want, we will get it done whatever you want.</p></div>
    <div class="step-number">1</div>
  </section>

  <section class="step step-2">
    <div class="step-art" role="img" aria-label="Illustration of a woman customizing dress options on a screen"></div>
    <h2 class="step-tab tab-dark"><em>STEP 2:</em> Customization</h2>
    <div class="step-card"><p>Everyone is different; hence we realise the need for customization of the design and size. Here you select exactly how you want your dress to be. From sleeves to cuts, every­thing will be done as per your wish. Enter your measurements, lo and behold! You’re done. Leave your comments for even more customization.</p></div>
    <div class="step-number">2</div>
  </section>

  <section class="step step-3">
    <div class="step-art" role="img" aria-label="Illustration of a designer consulting a client in front of a mirror"></div>
    <h2 class="step-tab tab-pink"><em>STEP 3:</em> Designer Consultation</h2>
    <div class="step-card"><p>We as a user-friendly brand, aspire to provide the best of services to our clients. Our expert lady designers will help you for everything right from selecting of fabric to design of dress to necessary accessories. Our designers are just a call away!</p></div>
    <div class="step-number">3</div>
  </section>

  <section class="step step-4">
    <div class="step-art" role="img" aria-label="Illustration of tailors stitching and a courier delivering a parcel to a customer"></div>
    <h2 class="step-tab tab-dark"><em>STEP 4:</em> Stitch And Deliver</h2>
    <div class="step-card"><p>After you have placed your order, we confirm and verify the details. The boutique completes your order, sends it to us and we deliver it to your doorstep. We also have a team of designers in-house to cater to your customization.</p></div>
    <div class="step-number">4</div>
  </section>
</main>
</body>
</html>
```